Candle Rental Business seeks new website design

We need a new website design for a Candle hire business. The business rents out pillar candles for events such as weddings and corporate events. Our main target market is weddings. The business name is Hire a Lantern. The business name does not have a logo design.

We would like a website that is light in colours and creates a warm atmosphere. The design needs to be elegant and upmarket. There are different size candles that we hire out, ranging from 10cm diameter to 20cm diameter, flat, tall etc. All our candles are white in colour. Its just the size that differs.

We would also like to include a section for hiring out decor such as glassvases, candlebras, overlays and chairs sachets, chair covers. However, this is not the businesses main focus but an additional offering to customers.

Target Market(s)

Wedding venues and brides. Corporate events. School dances.

Industry/Entity Type

Hospitality

Logo Text

Hire a Lantern

Number of Pages Required

1 page

Font styles to use
Sans Serif
Script

Requirements
Must have
• Pictures of pillar candles. Plain white candles. The website must centre around candles.
Nice to have
• Different examples of candle centrepieces
Should not have
• Pictures must not be of brides. Pictures of surrounding is perferable.

```html
<!DOCTYPE html>
<html lang="en">
<head>
<meta charset="utf-8">
<title>Hire a Lantern — Candle Hire</title>
<link href="https://fonts.googleapis.com/css2?family=Great+Vibes&family=Montserrat:wght@400;600;700;800&family=Open+Sans:wght@400;600&display=swap" rel="stylesheet">
<style>
:root{
  --pink:#f27ab0;
  --pink-soft:#f7a8cc;
  --purple:#a667d6;
  --purple-deep:#7d3fb0;
  --lilac:#c48be6;
  --violet-band:#5b2a6e;
  --ink:#3a3a3a;
  --muted:#8a8a8a;
  --grey-bg:#eeeeee;
  --footer:#2c2c2c;
  --footer-deep:#1f1f1f;
  --white:#ffffff;
}
*{box-sizing:border-box;margin:0;padding:0}
html,body{width:1200px;height:3184px;overflow:hidden}
body{font-family:'Open Sans',sans-serif;color:var(--ink);background:var(--white);font-size:13px;line-height:1.6}
.script{font-family:'Great Vibes',cursive}

/* header */
.site-header{height:100px;background:var(--pink);position:relative;color:var(--white)}
.topline{position:absolute;right:40px;top:8px;font-size:11px;display:flex;gap:22px;align-items:center}
.topline svg{vertical-align:middle;margin-right:5px}
.brand{position:absolute;left:40px;top:28px;display:flex;align-items:center;gap:12px;font-family:'Montserrat',sans-serif;font-weight:700;font-size:24px}
.brand .dot{width:26px;height:26px;border-radius:50%;background:var(--white)}
.nav{position:absolute;right:40px;top:58px;display:flex;gap:30px;font-family:'Montserrat',sans-serif;font-size:11px;font-weight:600;letter-spacing:.5px}

/* hero */
.hero{height:430px;position:relative;background:linear-gradient(180deg,#3a2a3a 0%,#8a6f78 35%,#d9c6c8 70%,#b89aa6 100%)}
.hero-badge{position:absolute;left:290px;top:95px;width:240px;height:240px;border-radius:50%;background:rgba(255,255,255,.85);border:3px solid rgba(255,255,255,.6);text-align:center;padding-top:56px}
.hero-badge h1{font-size:50px;color:var(--purple-deep);font-weight:400;line-height:1}
.hero-badge p{font-family:'Montserrat',sans-serif;font-size:12px;font-weight:600;color:#555;padding:12px 36px 0;line-height:1.5}
.arrow{position:absolute;top:195px;width:34px;height:40px;background:rgba(0,0,0,.45);display:flex;align-items:center;justify-content:center}
.arrow.l{left:0}.arrow.r{right:0}

/* features */
.features{display:flex;height:280px}
.feature{flex:1;text-align:center;color:var(--white);padding-top:44px}
.feature:nth-child(1){background:var(--lilac)}
.feature:nth-child(2){background:var(--purple)}
.feature:nth-child(3){background:#c589df}
.feature h2{font-family:'Montserrat',sans-serif;font-size:28px;font-weight:700;margin-top:12px}
.feature p{font-size:12px;padding:6px 70px 0;line-height:1.5}
.feature .btn{display:inline-block;width:26px;height:22px;background:var(--white);margin-top:14px}

/* section titles */
.sec-title{text-align:center;font-family:'Montserrat',sans-serif;font-size:32px;font-weight:700;color:#555;display:flex;justify-content:center;align-items:center;gap:16px}
.sec-title em{font-style:normal;color:var(--pink)}
.sec-title .rule{width:36px;height:2px;background:#ccc}

/* welcome */
.welcome{height:460px;padding-top:50px}
.welcome-body{display:flex;gap:40px;padding:50px 140px 0}
.welcome-photo{width:220px;height:220px;border-radius:50%;flex:none;background:radial-gradient(circle at 45% 45%,#fffaf0,#d8d2c6 60%,#9aa58c)}
.welcome-text .lead{color:var(--pink);font-family:'Montserrat',sans-serif;font-weight:600;font-size:13px;margin-bottom:12px}
.welcome-text p{font-size:12px;color:var(--muted);margin-bottom:12px}
.read{font-size:11px;color:var(--pink);font-weight:600}

/* decor */
.decor{height:620px;background:var(--grey-bg);padding-top:50px}
.decor-body{display:flex;padding:40px 140px 0;gap:60px}
.decor-chart{width:420px;height:420px;flex:none}
.decor-list{padding-top:10px}
.decor-item{display:flex;gap:20px;margin-bottom:34px}
.decor-icon{width:52px;height:52px;border-radius:50%;background:#b9b9b9;flex:none;display:flex;align-items:center;justify-content:center}
.decor-item h3{font-family:'Montserrat',sans-serif;font-size:16px;color:#666;font-weight:600}
.decor-item p{font-size:12px;color:var(--muted);width:340px}

/* design band */
.craft{height:540px;background:linear-gradient(90deg,#3c2040 0%,var(--violet-band) 50%,#7a3f8a 100%);position:relative;color:var(--white)}
.craft-photo{position:absolute;left:0;top:0;width:500px;height:540px;background:radial-gradient(ellipse at 55% 60%,#fff3e6 0%,#e8cfc0 22%,#8a5d80 55%,transparent 80%)}
.craft-text{position:absolute;left:520px;top:130px;width:540px;font-family:'Montserrat',sans-serif}
.craft-text h2{font-size:21px;font-weight:700;line-height:1.3;text-transform:none}
.craft-text .sub{font-size:17px;font-weight:600;line-height:1.4;margin-top:4px}
.craft-text .sizes{font-size:18px;font-weight:700;line-height:1.4;margin-top:26px;color:#f5d9ff}
.shop{position:absolute;left:580px;top:380px;width:92px;height:92px;border-radius:50%;background:var(--pink);display:flex;align-items:center;justify-content:center;font-family:'Montserrat',sans-serif;font-weight:700;font-size:13px;border:5px solid rgba(255,255,255,.35)}

/* testimonials */
.clients{height:320px;padding-top:44px}
.quote{display:flex;align-items:center;gap:30px;padding:50px 140px 0}
.quote-photo{width:90px;height:90px;border-radius:50%;background:linear-gradient(135deg,#e9d7c8,#9fae8a);border:4px solid #f0f0f0;flex:none}
.quote-who{width:160px;flex:none}
.quote-who b{display:block;font-family:'Montserrat',sans-serif;color:var(--purple);font-size:15px}
.quote-who span{font-size:11px;color:var(--muted)}
.quote-text{font-size:12px;color:var(--muted);border-left:2px solid #ddd;padding-left:24px}
.dots{display:flex;justify-content:center;gap:8px;margin-top:34px}
.dots i{width:9px;height:9px;border-radius:50%;background:#ccc}
.dots i:first-child{background:var(--purple)}

/* partners */
.partners{height:120px;border-top:1px solid #e6e6e6;display:flex;justify-content:center;align-items:center;gap:40px}
.partners span{width:130px;height:40px;background:#e2e2e2;border-radius:20px}

/* footer */
.footer{height:304px;background:var(--footer);color:#cfcfcf;position:relative}
.footer-top{height:8px;background:linear-gradient(90deg,var(--pink),var(--purple))}
.cols{display:flex;gap:50px;padding:36px 140px 0}
.col{width:200px;font-size:11px}
.col h4{font-family:'Montserrat',sans-serif;color:var(--white);font-size:12px;letter-spacing:.5px;margin-bottom:14px}
.col li{list-style:none;margin-bottom:4px}
.col li::before{content:"› ";color:var(--pink)}
.field{height:24px;background:var(--white);margin:10px 0 8px}
.sub-btn{display:inline-block;background:var(--purple);color:var(--white);padding:3px 12px;font-size:10px;font-weight:600}
.news{display:flex;gap:10px;margin-bottom:14px}
.news i{width:12px;height:12px;border-radius:50%;background:#888;flex:none;margin-top:3px}
.foot-brand{font-family:'Montserrat',sans-serif;color:var(--white);font-weight:700;font-size:17px;display:flex;align-items:center;gap:8px;margin-bottom:10px}
.foot-brand .dot{width:16px;height:16px;border-radius:50%;background:var(--white)}
.contact-row{display:flex;align-items:center;gap:8px;margin-bottom:4px}
.social{position:absolute;right:160px;top:230px;display:flex;gap:6px}
.social i{width:20px;height:20px;background:var(--purple)}
.copyright{position:absolute;left:0;bottom:0;width:100%;height:40px;background:var(--footer-deep);font-size:10px;color:#999;padding:12px 140px}
</style>
</head>
<body>

<header class="site-header">
  <div class="topline">
    <span><svg width="11" height="11" viewBox="0 0 24 24"><path fill="#fff" d="M6.6 10.8a15 15 0 006.6 6.6l2.2-2.2c.3-.3.7-.4 1-.2 1.1.4 2.3.6 3.6.6.6 0 1 .4 1 1V20c0 .6-.4 1-1 1A17 17 0 013 4c0-.6.4-1 1-1h3.5c.6 0 1 .4 1 1 0 1.3.2 2.5.6 3.6.1.3 0 .7-.2 1z"/></svg>555 014 2200</span>
    <span><svg width="12" height="10" viewBox="0 0 24 18"><rect x="1" y="1" width="22" height="16" fill="none" stroke="#fff" stroke-width="2"/><path d="M1 1l11 9 11-9" fill="none" stroke="#fff" stroke-width="2"/></svg>hello@hirealantern.example</span>
  </div>
  <div class="brand"><span class="dot"></span>Hire a Lantern</div>
  <nav class="nav"><span>HOME</span><span>ABOUT US</span><span>OUR PRODUCTS</span><span>HIRE CANDLES</span><span>DECOR HIRE</span><span>CONTACT</span></nav>
</header>

<section class="hero" role="img" aria-label="Floating candles in glass vases with orchids on a reception table">
  <div class="arrow l"><svg width="12" height="16"><path d="M10 2L3 8l7 6" stroke="#fff" stroke-width="2" fill="none"/></svg></div>
  <div class="hero-badge">
    <h1 class="script">Decorative Candles</h1>
    <p>Creating A Warm Atmosphere &amp; Special Touch To All Occasions.</p>
  </div>
  <div class="arrow r"><svg width="12" height="16"><path d="M2 2l7 6-7 6" stroke="#fff" stroke-width="2" fill="none"/></svg></div>
</section>

<section class="features">
  <div class="feature">
    <svg width="60" height="44" viewBox="0 0 60 44"><rect x="14" y="16" width="10" height="26" fill="none" stroke="#fff" stroke-width="2"/><rect x="28" y="10" width="10" height="32" fill="none" stroke="#fff" stroke-width="2"/><rect x="42" y="20" width="10" height="22" fill="none" stroke="#fff" stroke-width="2"/></svg>
    <h2>Hire Candles</h2>
    <p>Pillar candles for weddings, venues and events, delivered and collected.</p>
    <span class="btn"></span>
  </div>
  <div class="feature">
    <svg width="60" height="44" viewBox="0 0 60 44"><rect x="10" y="14" width="14" height="28" fill="none" stroke="#fff" stroke-width="2"/><rect x="34" y="8" width="14" height="34" fill="none" stroke="#fff" stroke-width="2"/></svg>
    <h2>Personalised Candles</h2>
    <p>Names, dates and monograms added to every candle you choose.</p>
    <span class="btn"></span>
  </div>
  <div class="feature">
    <svg width="60" height="44" viewBox="0 0 60 44"><path d="M20 42h20M30 42V14M14 14h32" stroke="#fff" stroke-width="2" fill="none"/><circle cx="14" cy="10" r="3" fill="#fff"/><circle cx="30" cy="10" r="3" fill="#fff"/><circle cx="46" cy="10" r="3" fill="#fff"/></svg>
    <h2>Décor Hire</h2>
    <p>Vases, candelabras, overlays and chair covers to finish the room.</p>
    <span class="btn"></span>
  </div>
</section>

<section class="welcome">
  <h2 class="sec-title"><span class="rule"></span>Welcome To <em>Hire a Lantern</em><span class="rule"></span></h2>
  <div class="welcome-body">
    <div class="welcome-photo" role="img" aria-label="White pillar candles with flowers on a table"></div>
    <div class="welcome-text">
      <p class="lead">Candles Create A Warm Atmosphere And Special Touch To All Occasions In Much Cheaper Renting Than Buying Candles For Your Event.</p>
      <p>We DESIGN, MANUFACTURE and PERSONALISE all of our CANDLES in our most distinctive handcrafted manner. Whether you are planning a wedding, a birthday, an anniversary, an engagement, a corporate function or a school dance, our elegant candles and decorative pieces help you create a space your guests will remember for years.</p>
      <p>We are a family owned and operated business proud to bring beautiful lighting to every venue. All of our candles are white and made to last through many events, so you only pay for the glow you need on the day.</p>
      <span class="read">READ MORE</span>
    </div>
  </div>
</section>

<section class="decor">
  <h2 class="sec-title"><span class="rule"></span>Our <em>Hiring Out Decor</em><span class="rule"></span></h2>
  <div class="decor-body">
    <svg class="decor-chart" viewBox="0 0 420 420" role="img" aria-label="Ring diagram of decor hire items">
      <circle cx="210" cy="210" r="180" fill="none" stroke="#9a6fc7" stroke-width="3" stroke-dasharray="4 6"/>
      <path d="M210 70a140 140 0 0 1 140 140h-70a70 70 0 0 0-70-70z" fill="#f27ab0"/>
      <path d="M350 210a140 140 0 0 1-140 140v-70a70 70 0 0 0 70-70z" fill="#ef8fbf"/>
      <path d="M210 350a140 140 0 0 1-140-140h70a70 70 0 0 0 70 70z" fill="#f7a8cc"/>
      <path d="M70 210a140 140 0 0 1 140-140v70a70 70 0 0 0-70 70z" fill="#f38db9"/>
      <g stroke="#fff" stroke-width="4"><line x1="210" y1="70" x2="210" y2="140"/><line x1="350" y1="210" x2="280" y2="210"/><line x1="210" y1="350" x2="210" y2="280"/><line x1="70" y1="210" x2="140" y2="210"/></g>
      <circle cx="210" cy="210" r="62" fill="#a667d6" stroke="#fff" stroke-width="6"/>
      <rect x="198" y="192" width="24" height="36" fill="none" stroke="#fff" stroke-width="3"/>
      <path d="M210 176c5 6 5 10 0 13-5-3-5-7 0-13z" fill="#fff"/>
      <g font-family="Montserrat,sans-serif" font-size="13" font-weight="600" fill="#fff" text-anchor="middle">
        <text x="272" y="140">Glass Vases</text>
        <text x="272" y="290">Candle Bras</text>
        <text x="148" y="290">Chair Covers</text>
        <text x="148" y="140">Overlays</text>
      </g>
      <g fill="#a667d6"><circle cx="210" cy="30" r="7"/><circle cx="390" cy="210" r="7"/><circle cx="210" cy="390" r="7"/><circle cx="30" cy="210" r="7"/></g>
    </svg>
    <div class="decor-list">
      <div class="decor-item"><div class="decor-icon"><svg width="22" height="26"><path d="M5 2h12l-2 22H7z" fill="none" stroke="#fff" stroke-width="2"/></svg></div><div><h3>Glass Vases</h3><p>Tall and short glass vases for floating candles and floral centrepieces.</p></div></div>
      <div class="decor-item"><div class="decor-icon"><svg width="26" height="26"><path d="M13 24V8M4 10h18M8 24h10" stroke="#fff" stroke-width="2" fill="none"/></svg></div><div><h3>Candle Bras</h3><p>Elegant candelabras to lift the table and frame each centrepiece.</p></div></div>
      <div class="decor-item"><div class="decor-icon"><svg width="24" height="24"><rect x="3" y="5" width="18" height="14" fill="none" stroke="#fff" stroke-width="2"/></svg></div><div><h3>Overlays &amp; Chair Sachets</h3><p>Soft table overlays and chair sashes in colours to match your theme.</p></div></div>
      <div class="decor-item"><div class="decor-icon"><svg width="22" height="26"><path d="M5 2h12v12H5zM5 14v10M17 14v10" stroke="#fff" stroke-width="2" fill="none"/></svg></div><div><h3>Chair Covers</h3><p>Fitted white chair covers that give every seat a clean finish.</p></div></div>
    </div>
  </div>
</section>

<section class="craft">
  <div class="craft-photo" role="img" aria-label="Lit white pillar candles on a dark purple backdrop"></div>
  <div class="craft-text">
    <h2>We DESIGN, MANUFACTURE &amp; PERSONALISE</h2>
    <p class="sub">All Of Our CANDLES In Our Most Distinctive<br>Handcrafted Manner!</p>
    <p class="sizes">Different Size Candles Ranging From<br>10cm Diameter To 20cm Diameter, Flat, Tall Etc</p>
  </div>
  <div class="shop">SHOP NOW</div>
</section>

<section class="clients">
  <h2 class="sec-title"><span class="rule"></span>What <em>Our Clients Say</em><span class="rule"></span></h2>
  <div class="quote">
    <div class="quote-photo" role="img" aria-label="Client portrait"></div>
    <div class="quote-who"><b>Dana Whitcombe</b><span>Events Manager</span></div>
    <p class="quote-text">“The candles turned our reception hall into something magical. Delivery was on time, every candle was spotless and the team helped us choose the right sizes for each table. Guests kept asking where the lighting came from, and we will book again for our next function.”</p>
  </div>
  <div class="dots"><i></i><i></i><i></i></div>
</section>

<section class="partners" aria-label="Partners">
  <span></span><span></span><span></span><span></span><span></span><span></span>
</section>

<footer class="footer">
  <div class="footer-top"></div>
  <div class="cols">
    <div class="col"><h4>QUICK LINK</h4><ul><li>Home</li><li>About Us</li><li>Our Products</li><li>Hire Candles</li><li>Décor Hire</li><li>Contact</li></ul></div>
    <div class="col"><h4>NEWSLETTER SIGN UP</h4><p>Join our list for new candle styles and seasonal offers.</p><div class="field"></div><span class="sub-btn">SUBSCRIBE</span></div>
    <div class="col"><h4>LATEST NEWS</h4>
      <div class="news"><i></i><div>New 20cm pillar range<br>March 12</div></div>
      <div class="news"><i></i><div>Winter wedding styling ideas<br>February 28</div></div>
      <div class="news"><i></i><div>School dance packages open<br>February 10</div></div>
    </div>
    <div class="col"><h4>GET IN TOUCH</h4>
      <div class="foot-brand"><span class="dot"></span>Hire a Lantern</div>
      <p>14 Willow Lane, Brookfield</p>
      <div class="contact-row"><svg width="10" height="10" viewBox="0 0 24 24"><path fill="#f27ab0" d="M6.6 10.8a15 15 0 006.6 6.6l2.2-2.2c.3-.3.7-.4 1-.2 1.1.4 2.3.6 3.6.6.6 0 1 .4 1 1V20c0 .6-.4 1-1 1A17 17 0 013 4c0-.6.4-1 1-1h3.5c.6 0 1 .4 1 1 0 1.3.2 2.5.6 3.6.1.3 0 .7-.2 1z"/></svg>555 014 2200</div>
      <div class="contact-row"><svg width="10" height="10" viewBox="0 0 24 24"><path fill="#f27ab0" d="M6.6 10.8a15 15 0 006.6 6.6l2.2-2.2c.3-.3.7-.4 1-.2 1.1.4 2.3.6 3.6.6.6 0 1 .4 1 1V20c0 .6-.4 1-1 1A17 17 0 013 4c0-.6.4-1 1-1h3.5c.6 0 1 .4 1 1 0 1.3.2 2.5.6 3.6.1.3 0 .7-.2 1z"/></svg>555 014 2201</div>
    </div>
  </div>
  <div class="social"><i></i><i></i><i></i><i></i></div>
  <div class="copyright">Copyright © Hire a Lantern. All Rights Reserved.</div>
</footer>

</body>
</html>
```